Marlowe Group needs a business card

I would like the card to be simple but modern and elegant.
I like black and white.
or black and gold.
we are a private finance lender and also are involved in property and property developments.

please look at the business card photos i provided i would like M.G only one one side and all the other details on the other side use fonts that tie in with my theme.

Industry/Entity Type

Finance

Contact Information for Business Card

Marlowe Group (M.G) Daniel Marlowe M: 0413586207 E: danmarl@inboxmail.test

Font styles to use
Other font styles liked:
• Use fonts that would reflect our business

Colors
000000
ffffff

Requirements
Must have
• one side of details
• other side has either M.G or Marlowe Group like in the photos provided

```html
<!DOCTYPE html>
<html lang="en">
<head>
<meta charset="utf-8">
<title>Marlowe Group — Business Card</title>
<link rel="stylesheet" href="https://fonts.googleapis.com/css2?family=Jost:wght@300&family=Ubuntu:wght@700&family=Arimo&display=swap">
<style>
  :root {
    --ink: #000000;
    --paper: #ffffff;
    --backdrop: #eeeeee;
    --muted: #8a8a8a;
  }
  * { margin: 0; padding: 0; box-sizing: border-box; }
  html, body {
    width: 1200px;
    height: 1200px;
    overflow: hidden;
    background: var(--backdrop);
  }
  .canvas {
    position: relative;
    width: 1200px;
    height: 1200px;
  }
  .card {
    position: absolute;
    left: 240px;
    width: 720px;
    height: 440px;
  }
  /* Front */
  .card-front {
    top: 126px;
    background: var(--ink);
    display: flex;
    align-items: center;
    justify-content: center;
  }
  .front-wordmark {
    display: flex;
    align-items: center;
    gap: 18px;
    color: var(--paper);
    font-family: "Ubuntu", sans-serif;
    font-weight: 700;
    font-size: 44px;
    letter-spacing: 1px;
  }
  .front-wordmark .mark-square {
    width: 16px;
    height: 16px;
    background: var(--paper);
  }
  /* Back */
  .card-back {
    top: 632px;
    background: var(--paper);
  }
  .back-wordmark {
    position: absolute;
    right: 70px;
    top: 46px;
    font-family: "Ubuntu", sans-serif;
    font-weight: 700;
    font-size: 34px;
    line-height: 1;
    color: var(--ink);
  }
  .side-name {
    position: absolute;
    left: 676px;
    top: 28px;
    height: 386px;
    writing-mode: vertical-rl;
    transform: rotate(180deg);
    font-family: "Jost", sans-serif;
    font-weight: 300;
    font-size: 15px;
    letter-spacing: 23.5px;
    color: var(--muted);
    white-space: nowrap;
  }
  .edge-bar {
    position: absolute;
    right: 0;
    top: 0;
    width: 14px;
    height: 100%;
    background: var(--ink);
  }
  .contact {
    position: absolute;
    left: 48px;
    top: 274px;
    color: var(--ink);
  }
  .person-name {
    font-family: "Ubuntu", sans-serif;
    font-weight: 700;
    font-size: 33px;
    line-height: 1.2;
    letter-spacing: -0.3px;
  }
  .name-rule {
    width: 79px;
    height: 4px;
    background: var(--ink);
    margin-top: 4px;
  }
  .contact-lines {
    list-style: none;
    font-family: "Arimo", sans-serif;
    font-size: 26px;
    margin-top: 10px;
  }
  .contact-lines li { line-height: 40px; }
  .contact-lines .label { display: inline-block; width: 42px; }
</style>
</head>
<body>
  <main class="canvas">
    <section class="card card-front" aria-label="Card front">
      <div class="front-wordmark">
        <span class="mark-square"></span>
        <span>Marlowe Group</span>
      </div>
    </section>

    <section class="card card-back" aria-label="Card back">
      <div class="back-wordmark">Marlowe Group</div>
      <div class="side-name">MARLOWE GROUP</div>
      <div class="edge-bar"></div>
      <div class="contact">
        <h1 class="person-name">Daniel Marlowe</h1>
        <div class="name-rule"></div>
        <ul class="contact-lines">
          <li><span class="label">M:</span>0413586207</li>
          <li><span class="label">E:</span>danmarl@inboxmail.test</li>
        </ul>
      </div>
    </section>
  </main>
</body>
</html>
```